Envelope Design - Winner can do follow-up business

- Varnoko.com is a Swiss-based online store selling business shirts and accessories for business men
- Please visit the webpage to make yourself familiar with the company. Although the text is in German, with Plimbo translator you should be able to understand the main content.
- Our clients are mainly business men between 30 and 60 years old. Mostly with a high income working in the service industry (banking, insurance, lawyers, etc.). Sometimes there wives purchase the shirts for them ;-)
- The colors and the logo are given, as they are also used for the print materials (please see files in attachment)
- I am running several businesses and often need a talented web designer --> the winner gets substantial follow-up business
your task:
-for our company we need a new envelope design
-It should be simple and modern
-please use one of the logos in the followings.
-suprise me :)

```html
<!DOCTYPE html>
<html lang="en">
<head>
<meta charset="utf-8">
<title>Varnoko Envelope Set</title>
<link rel="stylesheet" href="https://fonts.googleapis.com/css2?family=Questrial&family=Open+Sans:wght@400&display=swap">
<style>
  :root {
    --backdrop: #4a2c1c;
    --paper: #ffffff;
    --paper-shade: #eceef1;
    --ink-black: #000000;
    --brand-red: #ee2d24;
    --brand-red-soft: #f5543f;
    --brand-gold: #e6d46b;
    --text-dark: #1c1c1c;
  }
  * { margin: 0; padding: 0; box-sizing: border-box; }
  html, body {
    width: 1200px;
    height: 942px;
    overflow: hidden;
    background: var(--backdrop);
  }
  .canvas {
    position: relative;
    width: 1200px;
    height: 942px;
  }
  .envelope {
    position: absolute;
    width: 962px;
    height: 452px;
    background: var(--paper);
    overflow: hidden;
  }
  .envelope-back-red { left: 206px; top: 39px; }
  .envelope-back-black {
    left: 116px; top: 226px;
    background: linear-gradient(110deg, var(--paper-shade), var(--paper) 90%);
  }
  .envelope-front { left: 36px; top: 455px; width: 964px; }

  .flap { position: absolute; left: 0; top: 0; width: 962px; height: 160px; }

  .flap-wordmark {
    position: absolute;
    left: 0; width: 962px;
    text-align: center;
    font-family: "Questrial", sans-serif;
    letter-spacing: 0.05em;
  }
  .flap-wordmark-red {
    top: 30px;
    font-size: 40px;
    color: var(--brand-red-soft);
  }
  .flap-wordmark-black {
    top: 44px;
    font-size: 44px;
    color: var(--brand-gold);
  }

  .front-header {
    position: absolute;
    left: 0; top: 0;
    width: 100%;
    height: 106px;
    background: var(--ink-black);
  }
  .front-wordmark {
    position: absolute;
    left: 33px; top: 56px;
    font-family: "Questrial", sans-serif;
    font-size: 31px;
    letter-spacing: 0.05em;
    color: var(--brand-gold);
  }
  .front-mark {
    position: absolute;
    left: 117px; top: 14px;
    width: 36px; height: 36px;
    background: var(--brand-red);
  }

  .contact-line {
    position: absolute;
    top: 402px;
    display: flex;
    align-items: center;
    gap: 10px;
    font-family: "Open Sans", sans-serif;
    font-size: 19px;
    color: var(--text-dark);
  }
  .contact-address { left: 28px; }
  .contact-web { left: 478px; }
  .contact-line svg { flex: none; }

  .footer-bands {
    position: absolute;
    left: 0; top: 430px;
    width: 964px; height: 22px;
  }
</style>
</head>
<body>
<main class="canvas">

  <section class="envelope envelope-back-red" aria-label="Envelope back with red flap">
    <svg class="flap" viewBox="0 0 962 160" aria-hidden="true">
      <path d="M0 0 H962 C952 30 948 62 905 74 L520 144 Q475 154 430 144 L62 82 C22 72 16 38 0 0 Z" fill="var(--brand-red)"/>
    </svg>
    <div class="flap-wordmark flap-wordmark-red">VARNOKO</div>
  </section>

  <section class="envelope envelope-back-black" aria-label="Envelope back with black flap">
    <svg class="flap" viewBox="0 0 962 160" aria-hidden="true">
      <path d="M0 0 H962 C952 30 948 62 905 74 L520 144 Q475 154 430 144 L62 82 C22 72 16 38 0 0 Z" fill="var(--ink-black)"/>
    </svg>
    <div class="flap-wordmark flap-wordmark-black">VARNOKO</div>
  </section>

  <section class="envelope envelope-front" aria-label="Envelope front">
    <header class="front-header">
      <span class="front-mark" aria-hidden="true"></span>
      <div class="front-wordmark">VARNOKO</div>
    </header>

    <p class="contact-line contact-address">
      <svg width="16" height="22" viewBox="0 0 16 22" aria-hidden="true">
        <path d="M8 0 C3.6 0 0 3.4 0 7.8 C0 13 8 22 8 22 C8 22 16 13 16 7.8 C16 3.4 12.4 0 8 0 Z" fill="var(--brand-red)"/>
        <circle cx="8" cy="7.8" r="3" fill="var(--paper)"/>
      </svg>
      Street Name, City Name, State Zipcode
    </p>

    <p class="contact-line contact-web">
      <svg width="22" height="22" viewBox="0 0 22 22" aria-hidden="true" fill="none" stroke="var(--brand-red)" stroke-width="1.6">
        <circle cx="11" cy="11" r="9.5"/>
        <ellipse cx="11" cy="11" rx="4.5" ry="9.5"/>
        <line x1="1.5" y1="11" x2="20.5" y2="11"/>
        <line x1="3" y1="6" x2="19" y2="6"/>
        <line x1="3" y1="16" x2="19" y2="16"/>
      </svg>
      www.varnoko.com
    </p>

    <svg class="footer-bands" viewBox="0 0 964 22" aria-hidden="true">
      <polygon points="0,0 455,0 428,22 0,22" fill="var(--brand-gold)"/>
      <polygon points="470,0 964,0 964,22 440,22" fill="var(--brand-red)"/>
    </svg>
  </section>

</main>
</body>
</html>
```